Looking for business card/letterhead/email signature

Take existing logo and create full design suite of collateral

Contact Information for Business Card

Use mock details that can be edited by us

Font styles to use
Sans Serif

```html
<!DOCTYPE html>
<html lang="en">
<head>
<meta charset="utf-8">
<title>Harlow Digital – Stationery Suite</title>
<link href="https://fonts.googleapis.com/css2?family=Roboto:wght@400;500;700&family=Didact+Gothic&display=swap" rel="stylesheet">
<style>
  :root {
    --navy: #0b4a8f;
    --accent: #2aa7dd;
    --ink: #333;
    --muted: #555;
    --stage: #dddddd;
    --paper: #ffffff;
  }
  * { box-sizing: border-box; margin: 0; padding: 0; }
  html, body { width: 1200px; height: 738px; overflow: hidden; }
  body { background: var(--stage); font-family: "Roboto", Arial, sans-serif; color: var(--ink); position: relative; }

  .sheet { position: absolute; background: var(--paper); box-shadow: 0 1px 4px rgba(0,0,0,.18); overflow: hidden; }
  .wave { position: absolute; left: 0; bottom: 0; display: block; }
  .wave-fill { fill: var(--navy); }
  .wave-line { fill: none; stroke: var(--navy); stroke-width: 1.2; }
  .web { position: absolute; left: 0; right: 0; text-align: center; color: #fff; letter-spacing: .32em; }

  .brand { position: absolute; display: flex; align-items: center; gap: 5px; color: var(--navy); font-weight: 700; white-space: nowrap; }
  .brand-dot { border-radius: 50%; background: var(--accent); flex: none; }
  .brand.on-dark { color: #fff; }

  .icon { width: 7px; height: 7px; fill: var(--navy); vertical-align: -1px; margin-right: 3px; }

  /* letterhead */
  .letterhead { left: 66px; top: 107px; width: 452px; height: 583px; }
  .letterhead .brand { left: 40px; top: 56px; font-size: 17px; }
  .letterhead .brand-dot { width: 9px; height: 9px; }
  .lh-contact { position: absolute; left: 332px; top: 37px; padding-left: 9px; border-left: 1px solid #bbb; font-size: 6px; line-height: 7.6px; color: var(--muted); font-style: normal; }
  .lh-contact .gap { height: 3px; }
  .letter { position: absolute; left: 40px; top: 170px; width: 376px; font-family: "Didact Gothic", "Century Gothic", sans-serif; color: #666; }
  .salutation { font-size: 11.5px; color: #444; margin-bottom: 21px; }
  .letter p { font-size: 6.4px; line-height: 9.6px; margin-bottom: 9.6px; }
  .letter .closing { margin-top: 17px; }
  .signature { position: absolute; left: 38px; top: 436px; width: 82px; height: 34px; background: linear-gradient(90deg, rgba(11,74,143,.12), rgba(11,74,143,.04)); border-radius: 4px; }
  .letterhead .web { bottom: 7px; font-size: 6.4px; }

  /* email signature */
  .email-sig { left: 582px; top: 107px; width: 521px; height: 80px; }
  .email-sig .brand { left: 29px; top: 30px; font-size: 15px; }
  .email-sig .brand-dot { width: 8px; height: 8px; }
  .sig-rule { position: absolute; top: 17px; width: 1px; height: 46px; background: #bbb; }
  .sig-name { position: absolute; left: 172px; top: 29px; text-align: center; color: var(--navy); }
  .sig-name strong { display: block; font-size: 11.5px; font-weight: 500; }
  .sig-name span { display: block; font-size: 8px; color: #333; }
  .sig-address { position: absolute; left: 266px; top: 27px; font-size: 7.6px; line-height: 9.2px; color: var(--muted); }
  .sig-contact { position: absolute; left: 405px; top: 22px; font-size: 7.6px; line-height: 9.8px; color: var(--muted); }

  /* business card */
  .card { width: 251px; height: 143px; top: 203px; }
  .card-front { left: 578px; }
  .card-front .brand { left: 22px; top: 52px; font-size: 15px; }
  .card-front .brand-dot { width: 8px; height: 8px; }
  .card-rule { position: absolute; left: 135px; top: 29px; width: 1px; height: 72px; background: #bbb; }
  .card-info { position: absolute; left: 148px; top: 30px; font-size: 5.8px; line-height: 7px; color: var(--muted); }
  .card-info .name { font-size: 8.8px; line-height: 9px; font-weight: 500; color: var(--navy); }
  .card-info .title { font-size: 6.4px; color: #333; margin-bottom: 5px; }
  .card-info .gap { height: 4px; }
  .card-info .icon { width: 5.5px; height: 5.5px; }
  .card-front .web { bottom: 2px; font-size: 6px; }
  .card-back { left: 850px; background: var(--navy); }
  .card-back .brand { left: 0; right: 0; justify-content: center; top: 60px; font-size: 14px; }
  .card-back .brand-dot { width: 8px; height: 8px; }
  .card-back .web { top: 122px; font-size: 5.8px; }

  /* envelope */
  .envelope-back { left: 576px; top: 362px; width: 530px; height: 231px; box-shadow: 0 1px 4px rgba(0,0,0,.12); }
  .flap { position: absolute; left: 0; top: 0; }
  .envelope-back .brand { left: 0; right: 0; justify-content: center; top: 32px; font-size: 14px; }
  .envelope-back .brand-dot { width: 7px; height: 7px; }
  .envelope-front { left: 549px; top: 458px; width: 530px; height: 230px; }
  .envelope-front .brand { left: 26px; top: 47px; font-size: 15px; }
  .envelope-front .brand-dot { width: 8px; height: 8px; }
  .env-address { position: absolute; left: 27px; top: 92px; font-size: 6.4px; line-height: 7.6px; color: var(--muted); }
</style>
</head>
<body>

<svg width="0" height="0" style="position:absolute" aria-hidden="true">
  <defs>
    <symbol id="i-phone" viewBox="0 0 10 10"><path d="M2 0.5 L4 2.5 L3 4 Q4.5 6 6 7 L7.5 6 L9.5 8 L8 9.5 Q3 9 0.5 2 Z"/></symbol>
    <symbol id="i-mobile" viewBox="0 0 10 10"><path d="M2.5 0 H7.5 V10 H2.5 Z M3.5 1.2 V7.8 H6.5 V1.2 Z"/></symbol>
    <symbol id="i-mail" viewBox="0 0 10 10"><path d="M0 2 H10 V8.5 H0 Z"/><path d="M0.6 2.4 L5 5.6 L9.4 2.4" fill="none" stroke="#fff" stroke-width="1"/></symbol>
    <symbol id="i-globe" viewBox="0 0 10 10"><circle cx="5" cy="5" r="4.8"/><path d="M5 0.2 V9.8 M0.2 5 H9.8" stroke="#fff" stroke-width=".8"/></symbol>
  </defs>
</svg>

<!-- Letterhead -->
<section class="sheet letterhead">
  <div class="brand">Harlow Digital<span class="brand-dot"></span></div>
  <address class="lh-contact">
    <div>Harlow Digital</div>
    <div>1420 Maple Court</div>
    <div>Juneau, Alaska 99801</div>
    <div class="gap"></div>
    <div><svg class="icon"><use href="#i-phone"/></svg>555 210 4821</div>
    <div><svg class="icon"><use href="#i-mail"/></svg>info@harlowdigital.com</div>
  </address>

  <div class="letter">
    <div class="salutation">Dear Mr. Clarke,</div>
    <p>Lorem ipsum dolor sit amet, consectetur adipiscing elit. Donec orci purus, luctus vitae dignissim eu, iaculis sed purus. Vivamus faucibus, ipsum nec aliquet viverra, leo mauris condimentum ligula, sit amet sagittis enim ligula quis arcu. Nam egestas tortor id nisi porttitor mattis. In tortor ante, ultricies in suscipit a, tempus non massa. Vivamus et auctor mi. Fusce vel massa nulla. Phasellus nec eros mauris, et scelerisque orci.</p>
    <p>Donec malesuada orci vitae nulla accumsan porta a id massa. Quisque accumsan iaculis magna sit amet fringilla. Maecenas consequat, magna eget tincidunt semper, odio nibh rutrum mi, id feugiat ante nisi eu risus. Vestibulum nunc orci, rhoncus a placerat in, ultricies in mi. Cras mattis varius eros, vel fringilla nisi suscipit eget. Quisque scelerisque sagittis nulla at porttitor.</p>
    <p>Sed id augue vitae urna euismod commodo aliquet a quam. Pellentesque arcu velit, cursus et malesuada ut, consequat et diam. Nullam erat sem, rhoncus id ullamcorper vitae, rhoncus et arcu. In ultricies ultricies nulla, ut rutrum nisl iaculis at. Donec eu magna a metus ornare faucibus. Fusce aliquet faucibus ultricies. Morbi semper, est id tincidunt gravida, sem arcu adipiscing lacus, ac bibendum nulla leo eu purus. Quisque nec diam sed risus consectetur a accumsan quis quis nibh. Vestibulum id purus lorem.</p>
    <p>It is a long established fact that a reader will be distracted by the readable content of a page when looking at its layout. The point of using Lorem Ipsum is that it has a more-or-less normal distribution of letters, as opposed to using 'Content here, content here', making it look like readable English. Many desktop publishing packages</p>
    <p class="closing">Sincerely,</p>
  </div>
  <div class="signature" role="img" aria-label="Handwritten signature of Evan Clarke"></div>

  <svg class="wave" width="452" height="75" viewBox="0 0 452 75" aria-hidden="true">
    <path class="wave-fill" d="M0 6 Q226 98 452 6 L452 75 L0 75 Z"/>
    <path class="wave-line" d="M0 2 Q226 92 452 2"/>
  </svg>
  <div class="web">www.harlowdigital.com</div>
</section>

<!-- Email signature -->
<section class="sheet email-sig">
  <div class="brand">Harlow Digital<span class="brand-dot"></span></div>
  <div class="sig-rule" style="left:140px"></div>
  <div class="sig-name"><strong>EVAN CLARKE</strong><span>CEO/FOUNDER</span></div>
  <div class="sig-rule" style="left:248px"></div>
  <div class="sig-address">Harlow Digital<br>1420 Maple Court<br>Juneau, Alaska 99801</div>
  <div class="sig-rule" style="left:375px"></div>
  <div class="sig-contact">
    <div><svg class="icon"><use href="#i-phone"/></svg>555 210 4821</div>
    <div><svg class="icon"><use href="#i-mobile"/></svg>555 318 7750</div>
    <div><svg class="icon"><use href="#i-mail"/></svg>evan@harlowdigital.com</div>
    <div><svg class="icon"><use href="#i-globe"/></svg>www.harlowdigital.com</div>
  </div>
</section>

<!-- Business card front -->
<section class="sheet card card-front">
  <div class="brand">Harlow Digital<span class="brand-dot"></span></div>
  <div class="card-rule"></div>
  <div class="card-info">
    <div class="name">EVAN CLARKE</div>
    <div class="title">CEO/FOUNDER</div>
    <div>Harlow Digital</div>
    <div>1420 Maple Court</div>
    <div>Juneau, Alaska 99801</div>
    <div class="gap"></div>
    <div><svg class="icon"><use href="#i-phone"/></svg>555 210 4821</div>
    <div><svg class="icon"><use href="#i-mobile"/></svg>555 318 7750</div>
    <div><svg class="icon"><use href="#i-mail"/></svg>evan@harlowdigital.com</div>
  </div>
  <svg class="wave" width="251" height="36" viewBox="0 0 251 36" aria-hidden="true">
    <path class="wave-fill" d="M0 4 Q125.5 40 251 4 L251 36 L0 36 Z"/>
    <path class="wave-line" d="M0 1 Q125.5 36 251 1"/>
  </svg>
  <div class="web">www.harlowdigital.com</div>
</section>

<!-- Business card back -->
<section class="sheet card card-back">
  <div class="brand on-dark">Harlow Digital<span class="brand-dot"></span></div>
  <div class="web">www.harlowdigital.com</div>
</section>

<!-- Envelope back -->
<section class="sheet envelope-back">
  <svg class="flap" width="530" height="80" viewBox="0 0 530 80" aria-hidden="true">
    <path class="wave-fill" d="M0 0 H530 L518 66 Q516 77 504 77 H24 Q14 77 12 70 Z"/>
  </svg>
  <div class="brand on-dark">Harlow Digital<span class="brand-dot"></span></div>
</section>

<!-- Envelope front -->
<section class="sheet envelope-front">
  <div class="brand">Harlow Digital<span class="brand-dot"></span></div>
  <div class="env-address">Harlow Digital<br>1420 Maple Court<br>Juneau, Alaska 99801</div>
  <svg class="wave" width="530" height="68" viewBox="0 0 530 68" aria-hidden="true">
    <path class="wave-fill" d="M0 5 Q265 112 530 5 L530 68 L0 68 Z"/>
    <path class="wave-line" d="M0 1 Q265 106 530 1"/>
  </svg>
</section>

</body>
</html>
```